Quintel Packaging Business Card

Project Overview
We are seeking a modern, minimalist business card that effectively represents our company while making a bold and lasting impression. The design should reflect trust, professionalism, and innovation, reinforcing our expertise in custom plastic manufacturing for warehouse and distribution centers.

Provided Assets & Specifications
Logo: We will provide our official logo for integration into the design.
Design Files: Photoshop (PSD) files for our printing specifications will be supplied.

Card Size & Material:
Dimensions: 3.5" x 2"
Material: 1/8" Radius Plastic Business Cards with 1/8" Rounded Corners
Clear plastic background—the design should strategically incorporate transparency.
Orientation: The card should be designed in landscape format for a sleek and professional presentation.

Design Requirements:
Logo Prominence
The logo must be the focal point of the card.
Space should be used effectively to draw attention to the logo while maintaining a minimalist layout.

Clear Plastic Integration
The transparent background should create the illusion of blank space, enhancing the modern and high-quality feel.
Avoid any frosted effects—we do not want white areas to appear semi-transparent.

Minimalist & Impactful
Clean, structured, and easy to read at a glance.
Focus on sharp contrast to ensure legibility and visibility.
The design should instill confidence and reflect our role as a leading plastics manufacturer.

Color Palette & Contrast
Primary Colors: Blue, Black, White, and Grey
Use bold black or blue for text and key elements to ensure they stand out against the clear plastic.
Avoid light, pastel, or neon colors that may fade into the plastic background.
No frosted or semi-transparent white—we do not want a cloudy effect.

Typography & Information Hierarchy
Bold, modern typography—clear, professional, and highly legible.
The business card should highlight:
Company Logo (Primary Focus)
Full Name & Title
Phone Number
Email
Website

Brand Representation
The card should reflect our expertise in manufacturing high-quality custom plastics for large-scale packaging and distribution businesses.
Our clients rely on us to enhance their brand presence through custom plastic solutions, and our business cards should reinforce that sense of precision and trust.

Final Considerations
Utilize the clear plastic effectively to differentiate our brand from standard business cards.
Maintain a sleek, professional aesthetic while ensuring all text and elements remain legible.
The design should align with our industry, conveying reliability and innovation.
We look forward to seeing a design that captures our brand identity, maximizes the clear plastic medium, and makes a strong, professional impact on our clients.

```html
<!DOCTYPE html>
<html lang="en">
<head>
<meta charset="utf-8">
<title>Quintel Packaging Business Card</title>
<link href="https://fonts.googleapis.com/css2?family=Montserrat:wght@400;500;700;800&display=swap" rel="stylesheet">
<style>
  :root {
    --stage: #3a3a3c;
    --card-blue: #0689c0;
    --card-blue-deep: #05709f;
    --card-black: #161616;
    --accent-blue: #0b8fcf;
    --white: #ffffff;
  }
  * { margin: 0; padding: 0; box-sizing: border-box; }
  html, body {
    width: 1200px;
    height: 689px;
    overflow: hidden;
    background: var(--stage);
    font-family: "Montserrat", sans-serif;
  }
  .canvas {
    position: relative;
    width: 1200px;
    height: 689px;
    display: flex;
    align-items: center;
    justify-content: center;
    gap: 60px;
  }
  .card {
    position: relative;
    width: 525px;
    height: 300px;
    border-radius: 18px;
    overflow: hidden;
  }
  .card--front {
    background: var(--card-blue);
    display: flex;
    align-items: center;
    justify-content: center;
  }
  .brand {
    display: flex;
    align-items: center;
    gap: 18px;
  }
  .brand__square {
    flex: none;
  }
  .brand__name {
    font-weight: 800;
    line-height: 1.05;
    text-transform: uppercase;
  }
  .card--front .brand__square {
    width: 74px;
    height: 74px;
    background: var(--card-blue-deep);
  }
  .card--front .brand__name {
    color: var(--card-blue-deep);
    font-size: 38px;
    letter-spacing: 1px;
  }
  .card--back {
    background: var(--card-black);
    display: flex;
    align-items: center;
    padding: 0 34px 0 34px;
  }
  .card--back .brand {
    width: 230px;
    gap: 12px;
  }
  .card--back .brand__square {
    width: 40px;
    height: 40px;
    background: var(--white);
  }
  .card--back .brand__name {
    color: var(--white);
    font-size: 20px;
    letter-spacing: 0.5px;
  }
  .divider {
    width: 1.5px;
    height: 150px;
    background: var(--accent-blue);
    margin: 0 22px 0 10px;
  }
  .details {
    color: var(--white);
    font-size: 12.5px;
    line-height: 1.5;
  }
  .details__name {
    color: var(--accent-blue);
    font-weight: 800;
    font-size: 21px;
    letter-spacing: 0.5px;
    line-height: 1.1;
  }
  .details__title { margin-bottom: 10px; }
  .details__address { margin-bottom: 8px; }
  .contact {
    display: flex;
    align-items: center;
    gap: 7px;
  }
  .contact svg { width: 11px; height: 11px; flex: none; }
</style>
</head>
<body>
<main class="canvas">
  <section class="card card--front" aria-label="Card front">
    <div class="brand">
      <span class="brand__square"></span>
      <span class="brand__name">Quintel<br>Packaging</span>
    </div>
  </section>

  <section class="card card--back" aria-label="Card back">
    <div class="brand">
      <span class="brand__square"></span>
      <span class="brand__name">Quintel<br>Packaging</span>
    </div>
    <span class="divider"></span>
    <div class="details">
      <p class="details__name">DANA WHITFIELD</p>
      <p class="details__title">Managing Director</p>
      <p class="details__address">Your address, City<br>State, Zip 1234</p>
      <p class="contact">
        <svg viewBox="0 0 12 12" aria-hidden="true"><path fill="#0b8fcf" d="M2.5 1l2 2.2-1 1.3a6 6 0 0 0 4 4l1.3-1 2.2 2-1.3 1.5C5.5 11 1 6.5 1 2.3z"/></svg>
        123 456 789
      </p>
      <p class="contact">
        <svg viewBox="0 0 12 12" aria-hidden="true"><rect x="0.5" y="2" width="11" height="8" rx="1" fill="#0b8fcf"/><path d="M1 2.5l5 4 5-4" stroke="#161616" stroke-width="1" fill="none"/></svg>
        info@yourgmail.com
      </p>
      <p class="contact">
        <svg viewBox="0 0 12 12" aria-hidden="true"><circle cx="6" cy="6" r="5" fill="none" stroke="#0b8fcf" stroke-width="1.4"/><path d="M1 6h10M6 1c-2.5 3-2.5 7 0 10M6 1c2.5 3 2.5 7 0 10" stroke="#0b8fcf" stroke-width="1" fill="none"/></svg>
        www.yourwebsite.com
      </p>
    </div>
  </section>
</main>
</body>
</html>
```